New Business Card Design Project

We require a business card design for Vexalund, a newly established Indian company.
Our focus is on the development, manufacturing, and export of a diverse array of pharmaceutical products on a global scale. The card should convey a professional appearance, as our primary markets are in Africa, China, and Southeast Asian nations.
We envision a two-sided business card, with the reverse side dedicated to a logo set against a solid color or an elegantly designed pattern. The corners should be rounded. We would appreciate seeing both horizontal and vertical design options. We trust the designer to utilize their expertise in creating this design.

The content for the business card is included in the attached Word file.

Target Market(s)

Our primary markets are in Africa, China, and Southeast Asian, Latin America, Maldives, Sri Lanka

Industry/Entity Type

Pharmaceutical Manufacturing and Export

Contact Information for Business Card

Colors

Designer to choose colors to be used in the design.

Requirements
Must have
• The reverse side of the business card features solely the logo along with the tagline, "Care in Every Dose."
Should not have
• The logo should not exceed two instances, encompassing both the front and back sides of the card.

```html
<!DOCTYPE html>
<html lang="en">
<head>
<meta charset="utf-8">
<title>Vexalund Business Card</title>
<link rel="stylesheet" href="https://fonts.googleapis.com/css2?family=Open+Sans:wght@400;600;700&display=swap">
<style>
  :root {
    --backdrop: #232323;
    --card-white: #ebe9e7;
    --brand-blue: #2a95d3;
    --brand-red: #e05a45;
    --back-blue: #2ea7e0;
    --back-mark: #1c8fcf;
    --ink: #1b1b1b;
    --white: #ffffff;
  }
  * { margin: 0; padding: 0; box-sizing: border-box; }
  html, body {
    width: 1200px; height: 780px; overflow: hidden;
    background: var(--backdrop);
    font-family: "Open Sans", Arial, sans-serif;
  }
  .canvas {
    position: relative; width: 1200px; height: 780px;
    display: flex; align-items: center; justify-content: center; gap: 60px;
  }
  .card {
    position: relative; width: 520px; height: 300px;
    border-radius: 22px; overflow: hidden;
  }
  .card-front { background: var(--card-white); color: var(--ink); }
  .card-back { background: var(--back-blue); }

  .front-brand {
    position: absolute; left: 32px; top: 30px;
    display: flex; align-items: center; gap: 10px;
    font-weight: 700; font-size: 38px; line-height: 1.2;
    color: var(--brand-blue); letter-spacing: 0.5px;
  }
  .brand-dot { width: 14px; height: 14px; border-radius: 50%; background: var(--brand-red); }

  .contact {
    position: absolute; left: 32px; top: 104px;
    font-size: 13px; line-height: 19px; color: var(--ink);
    list-style: none;
  }
  .contact li { display: flex; align-items: center; gap: 7px; white-space: nowrap; }
  .contact .address { padding-left: 19px; }
  .contact svg { width: 12px; height: 12px; flex: none; }

  .holder {
    position: absolute; right: 58px; top: 190px; text-align: right;
  }
  .holder-name { font-size: 27px; font-weight: 600; letter-spacing: 0.5px; line-height: 1.2; white-space: nowrap; }
  .holder-first { color: var(--brand-blue); }
  .holder-last { color: var(--brand-red); font-weight: 400; }
  .holder-role { font-size: 15px; color: var(--ink); margin-top: 2px; }

  .edge-tab {
    position: absolute; right: 0; top: 240px; width: 26px; height: 42px;
    background: var(--brand-red);
  }

  .back-brand {
    position: absolute; left: 0; right: 0; top: 108px; text-align: center;
    font-weight: 700; font-size: 52px; line-height: 1.2;
    color: var(--back-mark); letter-spacing: 1px;
  }
  .tagline {
    position: absolute; left: 0; right: 0; top: 184px; text-align: center;
    font-size: 15px; color: var(--white); letter-spacing: 0.5px;
  }
</style>
</head>
<body>
<main class="canvas">
  <section class="card card-front" aria-label="Card front">
    <div class="front-brand"><span class="brand-name">Vexalund</span><span class="brand-dot"></span></div>
    <ul class="contact">
      <li class="address">14, Lotus Park Colony,</li>
      <li class="address">Nagpur, 440010, India</li>
      <li>
        <svg viewBox="0 0 12 12" aria-hidden="true"><rect x="1" y="1" width="10" height="10" fill="none" stroke="var(--brand-red)" stroke-width="1.3"/></svg>
        +91 98765 43210
      </li>
      <li>
        <svg viewBox="0 0 12 12" aria-hidden="true"><circle cx="6" cy="6" r="5" fill="none" stroke="var(--brand-blue)" stroke-width="1.3"/><path d="M1 6h10M6 1c-2.5 3-2.5 7 0 10M6 1c2.5 3 2.5 7 0 10" fill="none" stroke="var(--brand-blue)" stroke-width="1"/></svg>
        www.vexalund.com
      </li>
      <li>
        <svg viewBox="0 0 12 12" aria-hidden="true"><rect x="1" y="2.5" width="10" height="7" fill="var(--brand-red)"/><path d="M1 2.5l5 4 5-4" fill="none" stroke="var(--white)" stroke-width="1"/></svg>
        amehra@vexalund.com
      </li>
    </ul>
    <div class="holder">
      <div class="holder-name"><span class="holder-first">Arjun</span> <span class="holder-last">K. Mehra</span></div>
      <div class="holder-role">CEO</div>
    </div>
    <div class="edge-tab"></div>
  </section>

  <section class="card card-back" aria-label="Card back">
    <div class="back-brand">Vexalund</div>
    <div class="tagline">Care in Every Dose.</div>
  </section>
</main>
</body>
</html>
```